Market Research firm needs updated business cards with new logo

We need the logo to be included somewhere on the card (attached). We would also like the phrases "Independent, Objective, Comprehensive" and "Research You Can Trust" somewhere on the card. Front or back. Our colors are hex codes 6075a7, e48d25 and 5a5b5b. Though you are certainly not limited to those shades, whatever you produce should coordinate with them. I have also attached our favicon. Feel free to use it in your design, but please do not use it to replace the full logo.

Contact Information for Business Card

see project description

Font styles to use
Other font styles liked:
• Open Sans

Requirements
Must have
• the logo
• We use Open Sans font

```html
<!DOCTYPE html>
<html lang="en">
<head>
<meta charset="utf-8">
<title>Quenlow Research – Business Card</title>
<link href="https://fonts.googleapis.com/css2?family=Open+Sans:wght@400;600&family=Roboto:wght@400;500;700&family=EB+Garamond:wght@400&display=swap" rel="stylesheet">
<style>
  :root{
    --orange:#e08b25;
    --orange-line:#e48d25;
    --grey:#5a5b5b;
    --white:#ffffff;
    --stage:#504e4d;
  }
  *{box-sizing:border-box;margin:0;padding:0}
  html,body{width:1200px;height:960px;overflow:hidden;background:var(--stage)}
  .canvas{position:relative;width:1200px;height:960px}
  .card{position:absolute;left:240px;width:720px;height:410px;background:var(--orange);overflow:hidden;box-shadow:0 6px 18px rgba(0,0,0,.35)}
  .card--back{top:50px}
  .card--front{top:500px}
  .card__shapes{position:absolute;inset:0;width:100%;height:100%}
  .brand{position:absolute;display:flex;align-items:center;gap:9px;font-family:"Open Sans",sans-serif;font-weight:600;font-size:28px;color:var(--grey);letter-spacing:-.3px;white-space:nowrap}
  .brand__dot{width:15px;height:15px;border-radius:50%;background:var(--orange-line);flex:none}
  .card--back .brand{left:40px;top:180px}
  .card--front .brand{left:40px;top:188px}
  .tagline{position:absolute;left:410px;top:120px;width:160px;font-family:"EB Garamond",serif;font-size:15px;line-height:1.25;color:var(--white);text-align:center}
  .contact{position:absolute;left:460px;font-family:"Roboto",sans-serif;color:var(--grey)}
  .contact__name{top:60px;font-weight:700;font-size:25px;letter-spacing:.3px;line-height:1}
  .contact__title{top:89px;font-size:14px;font-weight:500}
  .contact__line{font-size:15px;line-height:1.3}
  .contact--phones{top:120px}
  .contact--web{top:175px}
  .contact--address{top:230px}
</style>
</head>
<body>
<main class="canvas">

  <section class="card card--back" aria-label="Business card back">
    <svg class="card__shapes" viewBox="0 0 720 410" aria-hidden="true">
      <polygon points="0,40 290,40 330,130 310,330 0,370" fill="var(--white)"/>
    </svg>
    <div class="brand"><span class="brand__dot"></span>Quenlow Research</div>
    <p class="tagline">Impartial, Rigorous<br>Thorough and<br>Insight Built on Evidence</p>
  </section>

  <section class="card card--front" aria-label="Business card front">
    <svg class="card__shapes" viewBox="0 0 720 410" aria-hidden="true">
      <polygon points="0,55 270,55 315,140 300,320 0,370" fill="var(--white)"/>
      <rect x="395" y="50" width="325" height="255" fill="var(--white)"/>
      <g stroke="var(--orange-line)" stroke-width="1.5">
        <line x1="395" y1="112" x2="720" y2="112"/>
        <line x1="395" y1="167" x2="720" y2="167"/>
        <line x1="395" y1="222" x2="720" y2="222"/>
      </g>
      <polygon class="icon-strip" points="340,112 400,112 445,150 445,305 405,305 405,160" fill="var(--grey)"/>
      <g stroke="var(--orange-line)" stroke-width="1.5">
        <line x1="382" y1="140" x2="430" y2="138"/>
        <line x1="405" y1="190" x2="445" y2="190"/>
        <line x1="405" y1="245" x2="445" y2="245"/>
      </g>
      <!-- mobile -->
      <rect x="371" y="115" width="10" height="18" rx="2" fill="var(--white)"/>
      <!-- phone handset -->
      <path d="M415 151 q-3 0 -3 4 q2 9 11 11 q4 0 4 -3 l-3 -3 l-3 2 q-4 -2 -5 -5 l2 -3 z" fill="var(--white)"/>
      <!-- globe -->
      <g fill="none" stroke="var(--white)" stroke-width="1.6">
        <circle cx="425" cy="217" r="10"/>
        <ellipse cx="425" cy="217" rx="4.5" ry="10"/>
        <line x1="415" y1="217" x2="435" y2="217"/>
      </g>
      <!-- pin -->
      <path d="M425 258 a8 8 0 0 1 8 8 c0 6 -8 14 -8 14 c0 0 -8 -8 -8 -14 a8 8 0 0 1 8 -8 z" fill="var(--white)"/>
      <circle cx="425" cy="266" r="3" fill="var(--grey)"/>
    </svg>
    <div class="brand"><span class="brand__dot"></span>Quenlow Research</div>
    <h1 class="contact contact__name">MARCUS ELWOOD</h1>
    <p class="contact contact__title">CHIEF EXECUTIVE</p>
    <div class="contact contact--phones">
      <p class="contact__line">+8801730418926</p>
      <p class="contact__line">+8801952307714</p>
    </div>
    <div class="contact contact--web">
      <p class="contact__line">www.elwoodinsight.com</p>
      <p class="contact__line">www.quenlowresearch.com</p>
    </div>
    <div class="contact contact--address">
      <p class="contact__line">Lakeview Road, Mirabel</p>
      <p class="contact__line">Eastport</p>
    </div>
  </section>

</main>
</body>
</html>
```